BRIGHT RIVER POWER.

I'd like my business logo.
contact name: Dennis Halvorsen
phone:0438759164
email: info@brightriverpower.net.au
website: www.brightriverpower.net.au

services:
solar
battery storage
LED lighting
energy saving solutions
general electrical
I'd like the design to look professional

Target Market(s)

Everyone

Industry/Entity Type

Business

Contact Information for Business Card

as described above

Requirements
Must have
• Id like the colours and the design to work well with my logo.

```html
<!DOCTYPE html>
<html lang="en">
<head>
<meta charset="UTF-8">
<title>Bright River Power – Business Cards</title>
<link href="https://fonts.googleapis.com/css2?family=Open+Sans:wght@400;600;700;800&display=swap" rel="stylesheet">
<style>
  :root {
    --page-bg: #e9e7e3;
    --orange-light: #f9a21f;
    --orange-deep: #ef8a12;
    --green-light: #8cc63f;
    --green-deep: #3d9a2f;
    --brand-green: #5cae33;
    --stripe-orange: #f29a1d;
    --card-white: #ffffff;
    --text-grey: #555555;
    --name-grey: #d9e6cf;
  }
  * { margin: 0; padding: 0; box-sizing: border-box; }
  html, body {
    width: 1200px;
    height: 843px;
    overflow: hidden;
    background: var(--page-bg);
    font-family: "Open Sans", Arial, sans-serif;
  }
  .canvas {
    position: relative;
    width: 1200px;
    height: 843px;
  }
  .card {
    position: absolute;
    top: 266px;
    width: 540px;
    height: 310px;
    border-radius: 24px;
    overflow: hidden;
    box-shadow: 0 10px 26px rgba(0, 0, 0, 0.18);
  }
  /* Front card */
  .card--front {
    left: 40px;
    background: linear-gradient(135deg, var(--orange-light), var(--orange-deep));
    color: #ffffff;
    display: flex;
    flex-direction: column;
    align-items: center;
    justify-content: center;
    gap: 26px;
  }
  .brand {
    display: flex;
    align-items: center;
    gap: 12px;
    font-weight: 800;
    letter-spacing: 0.5px;
  }
  .brand__dot {
    width: 22px;
    height: 22px;
    border-radius: 50%;
    flex: none;
  }
  .card--front .brand { font-size: 32px; color: #ffffff; }
  .card--front .brand__dot { background: #ffffff; }
  .services {
    font-size: 14px;
    font-weight: 400;
    letter-spacing: 0.6px;
  }
  .services span { margin: 0 6px; }
  /* Back card */
  .card--back {
    left: 620px;
    background: var(--card-white);
  }
  .card--back .brand {
    position: absolute;
    top: 48px;
    left: 70px;
    font-size: 28px;
    color: var(--brand-green);
  }
  .card--back .brand__dot { background: var(--stripe-orange); }
  .wave {
    position: absolute;
    inset: 0;
    width: 540px;
    height: 310px;
  }
  .contact {
    position: absolute;
    left: 38px;
    top: 150px;
    list-style: none;
    font-size: 15px;
    color: var(--text-grey);
    line-height: 24px;
  }
  .contact li {
    display: flex;
    align-items: center;
    gap: 10px;
  }
  .contact svg { width: 14px; height: 14px; flex: none; }
  .holder-name {
    position: absolute;
    right: 34px;
    bottom: 48px;
    font-size: 20px;
    font-weight: 700;
    color: var(--name-grey);
  }
</style>
</head>
<body>
<main class="canvas">

  <section class="card card--front" aria-label="Business card front">
    <div class="brand"><span class="brand__dot"></span>BRIGHT RIVER POWER</div>
    <p class="services">Solar<span>•</span>Battery Storage<span>•</span>LED Lighting</p>
  </section>

  <section class="card card--back" aria-label="Business card back">
    <svg class="wave" viewBox="0 0 540 310" aria-hidden="true">
      <defs>
        <linearGradient id="greenSweep" x1="0" y1="1" x2="1" y2="0">
          <stop offset="0" stop-color="var(--green-light)"/>
          <stop offset="1" stop-color="var(--green-deep)"/>
        </linearGradient>
      </defs>
      <path d="M215 310 C 300 200, 420 190, 540 96 L540 118 C 430 200, 320 220, 240 310 Z" fill="var(--stripe-orange)"/>
      <path d="M250 310 C 330 225, 440 205, 540 128 L540 310 Z" fill="url(#greenSweep)"/>
    </svg>

    <div class="brand"><span class="brand__dot"></span>BRIGHT RIVER POWER</div>

    <ul class="contact">
      <li>
        <svg viewBox="0 0 24 24" aria-hidden="true"><path fill="var(--brand-green)" d="M6.6 10.8a15.1 15.1 0 0 0 6.6 6.6l2.2-2.2a1 1 0 0 1 1-.25 11.4 11.4 0 0 0 3.6.57 1 1 0 0 1 1 1V20a1 1 0 0 1-1 1A17 17 0 0 1 3 4a1 1 0 0 1 1-1h3.5a1 1 0 0 1 1 1c0 1.25.2 2.45.57 3.57a1 1 0 0 1-.25 1z"/></svg>
        0438759164
      </li>
      <li>
        <svg viewBox="0 0 24 24" aria-hidden="true"><rect x="2" y="5" width="20" height="14" rx="2" fill="var(--brand-green)"/><path d="M3 6l9 7 9-7" stroke="#fff" stroke-width="1.8" fill="none"/></svg>
        info@brightriverpower.net.au
      </li>
      <li>
        <svg viewBox="0 0 24 24" aria-hidden="true"><circle cx="12" cy="12" r="10" fill="var(--brand-green)"/><path d="M2 12h20M12 2c3 3 3 17 0 20M12 2c-3 3-3 17 0 20" stroke="#fff" stroke-width="1.5" fill="none"/></svg>
        www.brightriverpower.net.au
      </li>
    </ul>

    <p class="holder-name">Dennis Halvorsen</p>
  </section>

</main>
</body>
</html>
```